Need a developer to develop and design my virtual employee recruitment solution website.

I need the entire website developed, from the design, the navigation, the contents of the website, etc. I need a professional looking website yet have that modern look. You can suggest the best fonts, color combinations to use. I need the site to be SEO friendly. I also want high quality stock photos to be used on the website. I wanted to achieve a similar website like this https://remotehelperpool.example/.

Target Market(s)

Ecommerce Entrepreneurs, Businessmen, Cartwell and Bazorra Sellers.

Industry/Entity Type

Professional Service

Coding

Coded - Design and coding required

Number of Pages Required

5+ page

Font styles to use
Sans Serif

Requirements
Must have
• I wanted it to have pages like this https://remotehelperpool.example/
Nice to have
• open for any recommendation you can suggest
Should not have
• Cannot think of any. You can suggest your own here

```html
<!DOCTYPE html>
<html lang="en">
<head>
<meta charset="utf-8">
<title>HelperPool – Virtual Staffing</title>
<link href="https://fonts.googleapis.com/css2?family=Montserrat:wght@400;500;600;700&family=Lato:wght@400;700&display=swap" rel="stylesheet">
<style>
:root{
  --blue:#0e6ad0;
  --blue-dark:#0a58b3;
  --ink:#1c1c1c;
  --text:#555;
  --white:#fff;
  --line:#d8d8d8;
}
*{box-sizing:border-box;margin:0;padding:0}
html,body{width:1200px;height:5217px;overflow:hidden}
body{position:relative;background:var(--white);font-family:"Lato",sans-serif;color:var(--text)}
.abs{position:absolute}
h1,h2,h3{font-family:"Montserrat",sans-serif}
.center{text-align:center;left:0;right:0}

/* header */
.brand{left:112px;top:44px;display:flex;align-items:center;gap:12px}
.brand-dot{width:22px;height:22px;border-radius:50%;background:var(--blue)}
.brand-name{font:700 24px "Montserrat",sans-serif;color:var(--blue)}
.search{left:482px;top:12px;width:300px;height:44px;border:1px solid var(--line);border-radius:22px;font-size:14px;color:#888;padding:13px 28px}
.search-btn{left:746px;top:12px;width:92px;height:44px;border-radius:22px;background:var(--blue);color:#fff;font-size:14px;text-align:center;line-height:44px}
.follow{left:852px;top:24px;font:600 16px "Montserrat",sans-serif;color:var(--ink)}
.social{top:18px;width:30px;height:30px;border-radius:50%;background:var(--blue)}
.contact-line{top:80px;font-size:16px;color:var(--ink);display:flex;align-items:center;gap:8px}
.flag{left:954px;top:76px;width:58px;height:28px;background:linear-gradient(#c8102e 0 50%,#f2f2f2 50%)}
.lang{left:1030px;top:82px;font-size:14px;color:var(--ink)}
.nav{left:0;top:118px;width:1200px;height:48px;background:var(--blue);display:flex;justify-content:space-between;padding:0 110px}
.nav a{color:#fff;text-decoration:none;font-size:16px;line-height:48px}
.nav a.active{text-decoration:underline;text-underline-offset:6px}

/* hero */
.hero{left:0;top:166px;width:1200px;height:558px;background:linear-gradient(100deg,#e9e7e4 0%,#dcd6cf 50%,#c9a86f 75%,#e8e4de 100%)}
.hero h1{left:112px;top:146px;font-size:38px;line-height:53px;font-weight:700;color:var(--ink);letter-spacing:.5px}
.hero h1 span{color:var(--blue)}
.btn{background:var(--blue-dark);color:#fff;font:600 16px "Montserrat",sans-serif;border-radius:26px;text-align:center}
.hero .btn{left:112px;top:322px;width:160px;height:48px;line-height:48px}
.arrow{top:248px;width:40px;height:40px;border:1px solid #bbb;border-radius:50%}

.lead{font:500 25px/35px "Montserrat",sans-serif;color:var(--blue)}
.para{font-size:15px;line-height:33px;color:var(--text)}
.sec-title{font:500 28px "Montserrat",sans-serif;color:var(--blue);letter-spacing:.5px}

.perks{left:602px;top:1690px;list-style:none;font-size:15px;color:#444;line-height:24px}
.perks li{display:flex;gap:12px;margin-bottom:13px;width:420px}
.perks li svg{flex:none;margin-top:4px}

.tag{height:52px;background:var(--blue);color:#fff;font:600 14px/1.2 "Montserrat",sans-serif;display:flex;align-items:center;justify-content:center;text-align:center;width:320px;padding:0 10px}

.band{left:0;width:1200px;background:linear-gradient(135deg,#2f7fd6 0%,#6aaae8 40%,#3b86d8 70%,#1c6bc7 100%)}
.band-title{font:400 23px/35px "Montserrat",sans-serif;color:#fff}
.card{background:#fff;width:302px;height:371px;padding:0 14px}
.avatar{width:96px;height:96px;border-radius:50%;background:linear-gradient(#9ec2e6,#4f6e8c);margin:26px auto 0}
.card p{font-size:12px;line-height:26px;color:#666;margin-top:34px}
.card .who{font:600 13px "Montserrat",sans-serif;color:var(--ink);margin-top:12px}
.card .role{font-size:12px;line-height:22px;color:#666}

.footer{left:0;top:4916px;width:1200px;height:301px;background:var(--blue)}
.footer h3{font-size:15px;font-weight:600;color:#fff}
.footer .list{font-size:14px;line-height:26px;color:#fff}
.copy{left:0;right:0;text-align:center;font-size:12px;color:#fff}
</style>
</head>
<body>

<header>
  <div class="abs brand"><span class="brand-dot"></span><span class="brand-name">HELPERPOOL</span></div>
  <div class="abs search">Search here...</div>
  <div class="abs search-btn">Search</div>
  <div class="abs follow">Follow Us :</div>
  <div class="abs social" style="left:946px"></div>
  <div class="abs social" style="left:982px"></div>
  <div class="abs social" style="left:1018px"></div>
  <div class="abs social" style="left:1054px"></div>
  <div class="abs contact-line" style="left:492px">
    <svg width="24" height="16" viewBox="0 0 24 16"><rect x="1" y="1" width="22" height="14" fill="none" stroke="#0e6ad0" stroke-width="2"/><path d="M1 1l11 8 11-8" fill="none" stroke="#0e6ad0" stroke-width="2"/></svg>
    info@helperpool.example
  </div>
  <div class="abs contact-line" style="left:744px">
    <svg width="18" height="18" viewBox="0 0 24 24"><path d="M6.6 10.8a15 15 0 006.6 6.6l2.2-2.2a1 1 0 011-.25 11 11 0 003.6.6 1 1 0 011 1V20a1 1 0 01-1 1A17 17 0 013 4a1 1 0 011-1h3.5a1 1 0 011 1 11 11 0 00.6 3.6 1 1 0 01-.25 1z" fill="#0e6ad0"/></svg>
    Call 888 - 888 - 8888
  </div>
  <div class="abs flag" role="img" aria-label="Language flag"></div>
  <div class="abs lang">English ⌄</div>
  <nav class="abs nav">
    <a class="active" href="#">Home</a><a href="#">About Us</a><a href="#">Services offered</a><a href="#">Pricing</a><a href="#">Testimonials</a><a href="#">FAQs</a><a href="#">Contact Us</a><a href="#">Blog</a>
  </nav>
</header>

<section class="abs hero" role="img" aria-label="Photo of a smiling woman working on a laptop at a bright desk">
  <h1 class="abs"><span>DON'T LET</span> YOUR BUSINESS<br>RUN YOU. <span>LEARN TO</span><br><span>DELEGATE.</span> HIRE A VA.</h1>
  <div class="abs btn">GET STARTED</div>
  <div class="abs arrow" style="left:38px"></div>
  <div class="abs arrow" style="left:1076px"></div>
</section>

<section>
  <p class="abs center lead" style="top:798px">Tired of being stuck in your 9-5 cubicle job? Exhausted from<br>commuting to and from the office? Want to spend more<br>time with your family? We've got you covered.</p>
  <p class="abs center para" style="top:922px">HelperPool is a virtual staffing company that helps freelancers and virtual assistants find their perfect work-from-home<br>job. We have a pool of clients from all over the world who are all looking for talented virtual assistants.</p>
  <div class="abs" style="left:174px;top:1014px;width:852px;height:415px;background:linear-gradient(90deg,#5d6f4e 0%,#cfd3d4 30%,#3c4a5a 60%,#e4e2dc 100%)" role="img" aria-label="Photo of a man on a video call at a desktop computer"></div>
</section>

<section>
  <h2 class="abs center sec-title" style="top:1506px">WITH HELPERPOOL, YOU GET TO:</h2>
  <p class="abs center para" style="top:1550px">Lorem ipsum dolor sit amet, consectetur adipiscing elit, sed do eiusmod tempor incididunt ut labore et dolore<br>magna aliqua. Quis ipsum suspendisse ultrices gravida.</p>
  <div class="abs" style="left:203px;top:1642px;width:294px;height:304px;background:radial-gradient(circle,#e8e2dc 0%,#f6f2ee 60%,#fff 100%)" role="img" aria-label="Illustration of a multitasking assistant holding office items"></div>
  <ul class="abs perks">
    <li><svg width="14" height="14" viewBox="0 0 14 14"><circle cx="7" cy="7" r="7" fill="#0e6ad0"/><path d="M5.5 4l3 3-3 3" stroke="#fff" stroke-width="1.8" fill="none"/></svg>Work from the comfort of your home</li>
    <li><svg width="14" height="14" viewBox="0 0 14 14"><circle cx="7" cy="7" r="7" fill="#0e6ad0"/><path d="M5.5 4l3 3-3 3" stroke="#fff" stroke-width="1.8" fill="none"/></svg>Have a competitive and steady income</li>
    <li><svg width="14" height="14" viewBox="0 0 14 14"><circle cx="7" cy="7" r="7" fill="#0e6ad0"/><path d="M5.5 4l3 3-3 3" stroke="#fff" stroke-width="1.8" fill="none"/></svg>Achieve work-life balance</li>
    <li><svg width="14" height="14" viewBox="0 0 14 14"><circle cx="7" cy="7" r="7" fill="#0e6ad0"/><path d="M5.5 4l3 3-3 3" stroke="#fff" stroke-width="1.8" fill="none"/></svg>Learn new skills for free</li>
    <li><svg width="14" height="14" viewBox="0 0 14 14"><circle cx="7" cy="7" r="7" fill="#0e6ad0"/><path d="M5.5 4l3 3-3 3" stroke="#fff" stroke-width="1.8" fill="none"/></svg>Work with a dedicated team who can provide you with HR, payroll, IT, and training assistance 24/7!</li>
  </ul>
</section>

<section>
  <h2 class="abs center sec-title" style="top:2036px">WHY WORK FOR HELPERPOOL?</h2>
  <p class="abs center para" style="top:2080px">Lorem ipsum dolor sit amet, consectetur adipiscing elit, sed do eiusmod tempor incididunt ut labore et dolore<br>magna aliqua. Quis ipsum suspendisse ultrices gravida.</p>
  <div class="abs tag" style="left:138px;top:2173px">COMPETITIVE HOURLY RATES</div>
  <div class="abs tag" style="left:112px;top:2236px">FLEXIBLE HOURS</div>
  <div class="abs tag" style="left:95px;top:2299px">FLEXIBLE SCHEDULE</div>
  <div class="abs tag" style="left:95px;top:2362px">WEEKLY PAYOUT VIA PAYLINK</div>
  <div class="abs tag" style="left:112px;top:2425px">PAYLINK FEES COVERED</div>
  <div class="abs tag" style="left:146px;top:2487px">VARIOUS POSITIONS AVAILABLE</div>
  <div class="abs tag" style="left:724px;top:2173px">FREE TRAINING &amp; UPSKILLING</div>
  <div class="abs tag" style="left:766px;top:2236px">NO PLACEMENT OR PROCESSING FEE</div>
  <div class="abs tag" style="left:784px;top:2299px">FLEXIBLE SCHEDULE</div>
  <div class="abs tag" style="left:784px;top:2362px">WORK FROM HOME</div>
  <div class="abs tag" style="left:768px;top:2425px">PAYROLL PROCESSING</div>
  <div class="abs tag" style="left:724px;top:2487px">CONTINUOUS RE-ASSIGNMENT<br>TO CLIENTS</div>
  <div class="abs" style="left:470px;top:2230px;width:260px;height:263px;background:linear-gradient(160deg,#f3f5f9,#dbe4f0)" role="img" aria-label="Illustration of a person working at a home office desk"></div>
</section>

<section>
  <h2 class="abs center sec-title" style="top:2618px">WHO ARE OUR VIRTUAL ASSISTANTS</h2>
  <p class="abs center" style="top:2666px;font-size:16px;color:var(--ink)">We have VAs from all over the Philippines</p>
  <div class="abs" style="left:174px;top:2726px;width:852px;height:412px;background:linear-gradient(90deg,#dfe2e4 0%,#bfb8ae 45%,#6a87b0 60%,#eceae6 100%)" role="img" aria-label="Photo of a woman on the phone at her home desk"></div>
  <p class="abs para" style="left:111px;top:3164px;width:460px">Our VA pool is composed of highly dedicated people armed with the right set of skills clients are looking for in a virtual assistant. We hire VAs of varying work experience and skill levels, and we help our VAs improve their skills so that they can get the jobs and clients they want.</p>
  <p class="abs para" style="left:620px;top:3164px;width:474px">HelperPool accepts VAs in a variety of niches. Currently, our VAs belongs to one or more of the following groups: Administrative VAs, eCommerce VAs, and Specialist VAs Are you ready to join the team? To start the application process, please click on the button below</p>
</section>

<section class="abs band" style="top:3422px;height:616px">
  <p class="abs center band-title" style="top:68px">Successful entrepreneurs hire great VAs.<br>Here's what our happy clients are saying about us.</p>
  <div class="abs card" style="left:113px;top:156px">
    <div class="avatar" role="img" aria-label="Client portrait"></div>
    <p>Lorem ipsum dolor sit et, ctetur adipiscing elit, sed do eiusmo d tempor incididunt ut labore et dolore magna aqua. Quis ipsu suspendisse ultricesavida. Risus commodo verra maecenas accumsan lacus vel facilisis.</p>
    <div class="who">JOHN SMITH</div>
    <div class="role">Owner, Creating Customers, LLC<br>Greater New York City Area</div>
  </div>
  <div class="abs card" style="left:450px;top:156px">
    <div class="avatar" role="img" aria-label="Client portrait"></div>
    <p>Lorem ipsum dolor sit et, ctetur adipiscing elit, sed do eiusmo d tempor incididunt ut labore et dolore magna aqua. Quis ipsu suspendisse ultricesavida. Risus commodo verra maecenas accumsan lacus vel facilisis.</p>
    <div class="who">JOHN SMITH</div>
    <div class="role">Owner, Creating Customers, LLC<br>Greater New York City Area</div>
  </div>
  <div class="abs card" style="left:786px;top:156px">
    <div class="avatar" role="img" aria-label="Client portrait"></div>
    <p>Lorem ipsum dolor sit et, ctetur adipiscing elit, sed do eiusmo d tempor incididunt ut labore et dolore magna aqua. Quis ipsu suspendisse ultricesavida. Risus commodo verra maecenas accumsan lacus vel facilisis.</p>
    <div class="who">JOHN SMITH</div>
    <div class="role">Owner, Creating Customers, LLC<br>Greater New York City Area</div>
  </div>
</section>

<section>
  <h2 class="abs center sec-title" style="top:4104px">SAVE 45-76% ON LABOR COST!</h2>
  <p class="abs center" style="top:4160px;font:700 17px/33px 'Lato',sans-serif;color:var(--ink)">Regular companies pay an average Administrative Assistant $31,000 yearly* or a web<br>designer/programmer $73,000 yearly*. With us, you ONLY<br>pay $17,056/year or $8.20/hour.</p>
  <div class="abs btn" style="left:460px;top:4271px;width:280px;height:47px;line-height:47px;font-size:15px">STARTING AT $8.20 PER HOUR.</div>
</section>

<section class="abs band" style="top:4393px;height:523px">
  <p class="abs center band-title" style="top:72px">From good business to great business.<br>The difference lies in hiring a reliable Virtual Assistant from us.</p>
  <div class="abs" style="left:142px;top:178px;width:253px;height:253px;border-radius:50%;border:5px solid var(--blue);background:linear-gradient(#c9dcef,#3d5d86)" role="img" aria-label="Client portrait"></div>
  <div class="abs" style="left:426px;top:152px;width:624px;height:283px;background:#fff;padding:38px 40px">
    <div style="font:600 13px 'Montserrat',sans-serif;color:var(--ink)">JOHN SMITH</div>
    <div style="font-size:12px;line-height:22px;color:#666;margin-top:12px">Owner, Creating Customers, LLC<br>Greater New York City Area</div>
    <p style="font-size:12px;line-height:25px;color:#666;margin-top:12px">Lorem ipsum dolor sit et, ctetur adipiscing elit, sed do eiusmo d tempor incididunt ut labore dolore magna aqua. Quis ipsu suspendisse ultricesavida. Risus commodo verra maecenas accumsan lacus vel facilisis. Lorem ipsum dolor sit et, ctetur adipiscing elit, sed do eiusmo d tempor incididunt ut labore et dolore magna aqua. Quis ipsu suspendisse ultricesavida. Risus commodo verra maecenas accumsan lacus vel facilisis.</p>
  </div>
</section>

<footer class="abs footer">
  <h3 class="abs" style="left:115px;top:72px">CONTACT US</h3>
  <div class="abs list" style="left:115px;top:106px">123 Avenue name, City name<br>10150, United States<br>888 888 8888<br>info@info@helperpool.example</div>
  <h3 class="abs" style="left:388px;top:72px">COMPANY INFO</h3>
  <div class="abs list" style="left:388px;top:106px">Home<br>About Us<br>Services offered<br>Pricing</div>
  <div class="abs list" style="left:526px;top:108px">Testimonials<br>FAQs<br>Contact Us<br>Blog</div>
  <p class="abs" style="left:672px;top:78px;width:430px;font-size:12px;line-height:26px;color:#fff">Lorem ipsum dolor sit amet, consectetur adipiscing elit, sed do eiusmod tempor incididunt ut labore et dolore magna aliqua.</p>
  <div class="abs" style="left:672px;top:140px;font:700 34px 'Montserrat',sans-serif;color:#fff">PayLink</div>
  <div class="abs" style="left:666px;top:192px;display:flex;gap:4px">
    <span style="width:24px;height:15px;background:#fff"></span><span style="width:24px;height:15px;background:#fff"></span><span style="width:24px;height:15px;background:#fff"></span><span style="width:24px;height:15px;background:#fff"></span><span style="width:24px;height:15px;background:#fff"></span><span style="width:24px;height:15px;background:#fff"></span><span style="width:24px;height:15px;background:#fff"></span>
  </div>
  <div class="abs" style="left:112px;top:250px;width:976px;height:1px;background:rgba(255,255,255,.3)"></div>
  <p class="abs copy" style="top:264px">Copyright © 2020 HelperPool. All Rights Reserved.</p>
</footer>

</body>
</html>
```